Building Referrer Relationships Booklet

4 page A4 booklet to give to potential professional referrers to establish a collaborative relationship.Needs to be bright, vibrant, colourful, friendly, inviting, in keeping with The Linden Practice colours.
Want to provide potential referrer partners a great reason to choose to collaborate with us. They need to know who we are, what makes us different/appealing, and who we are looking for to connect with.
The final product should communicate high performance and connectedness.
Updates

Target Market(s)

professional medical allied health and fitness practitioners

Industry/Entity Type

Health

Requirements
Must have
• energetic, vibrant, engaging, inviting, images

```html
<!DOCTYPE html>
<html lang="en">
<head>
<meta charset="utf-8">
<title>The Linden Practice – Our Pathway</title>
<link href="https://fonts.googleapis.com/css2?family=Arimo:wght@400;700&display=swap" rel="stylesheet">
<style>
:root{
  --ink:#1a1a1a;
  --accent:#e8400c;
  --badge:#dc4412;
  --white:#ffffff;
  --sky-top:#ffffff;
  --sky-mid:#f3f6f8;
  --sky-bottom:#d9eef6;
}
*{margin:0;padding:0;box-sizing:border-box}
html,body{width:1200px;height:895px;overflow:hidden;background:var(--white)}
body{font-family:"Arimo",Arial,sans-serif;color:var(--ink)}
.page{position:relative;width:1200px;height:895px;overflow:hidden}
.backdrop{position:absolute;inset:0;
  background:linear-gradient(180deg,var(--sky-top) 0%,var(--sky-mid) 45%,var(--sky-bottom) 62%,#e6f3f8 100%)}
.intro{position:absolute;left:40px;top:76px;width:760px;font-size:16px;line-height:21px}
.pathway{position:absolute;font-size:15px;line-height:20px}
.pathway--feet{left:40px;top:157px}
.pathway--body{left:676px;top:155px}
.pathway h2{color:var(--accent);font-size:15.5px;font-weight:700;margin-bottom:22px;line-height:20px}
.pathway--body h2{margin-bottom:20px}
.step{list-style:none}
.step>li{position:relative;padding-left:31px;margin-bottom:20px}
.step>li::before{content:attr(data-n) ".";position:absolute;left:0;top:0}
.step strong{font-weight:700}
.step ul{list-style:none;padding-left:28px}
.credentials{position:absolute;left:584px;top:700px;width:354px;height:180px;
  background:var(--badge);border-radius:24px;box-shadow:0 4px 10px rgba(0,0,0,.35);
  padding:16px 0 0 14px;color:var(--white);font-size:14px;line-height:18.7px;list-style:none}
.credentials li::before{content:"★"}
</style>
</head>
<body>
<div class="page">
  <div class="backdrop" role="img" aria-label="Faint pattern of medical icons: hospital signs, syringes, pill bottles, stethoscopes, eyeglasses and first-aid symbols"></div>

  <p class="intro">Our pathway to strengthen postural foundations, to create lasting changes for freedom of movement, and ultimately keep us going well beyond what we thought was possible (updated as research and tech changes).</p>

  <section class="pathway pathway--feet">
    <h2>FIX YOUR FEET</h2>
    <ol class="step">
      <li data-n="1"><strong>Fix</strong> the pain
        <ul>
          <li>Provide analgesia</li>
          <li>Reduce inflammation</li>
          <li>Corn/callus/foreign body removal</li>
          <li>Ingrown/thickened toenail repair and maintenance</li>
          <li>Surgery</li>
        </ul>
      </li>
      <li data-n="2"><strong>Protect</strong> the feet (reduce damage, optimise stability, promote healing)
        <ul>
          <li>Reduce tissue damage</li>
          <li>Optimise Foot Posture</li>
          <li>Activate neuromuscular/reflexive balance stability</li>
          <li>Promote tissue repair/cellular regeneration</li>
        </ul>
      </li>
      <li data-n="3"><strong>Strengthen</strong> the feet (increase strength and resilience)
        <ul>
          <li>Strengthen intrinsics</li>
          <li>Connect foot strength to core strength</li>
          <li>Stimulate neuromuscular strength</li>
        </ul>
      </li>
    </ol>
  </section>

  <section class="pathway pathway--body">
    <h2>BIOHACK YOUR BODY</h2>
    <ol class="step">
      <li data-n="1"><strong>Protect</strong> the whole body (stability)
        <ul>
          <li>Optimise Postural Alignment</li>
          <li>Activate neuromuscular/reflexive balance stability</li>
          <li>Customised corrective exercises</li>
          <li>Improve cellular regeneration</li>
          <li>Optimise nutrition/healthy gut</li>
          <li>Optimise healthy mind</li>
        </ul>
      </li>
      <li data-n="2"><strong>Strengthen</strong> the whole body (strength, elasticity)
        <ul>
          <li>Strengthen the deep core (stabilisers)</li>
          <li>Strengthen the outer core (mobilisers)</li>
          <li>Increase fascial elasticity/strength</li>
          <li>Increase functional strength</li>
          <li>Increase endurance</li>
          <li>Customised nutrition for specific performance</li>
          <li>Improve psychological resilience</li>
        </ul>
      </li>
      <li data-n="3"><strong>Repeat</strong> consistently</li>
    </ol>
  </section>

  <ul class="credentials">
    <li>Director, Sports Medicine Council (SMC)</li>
    <li>Director, Southern Academy of Podiatric Sports Medicine (SAPSM).</li>
    <li>External Advisor, Westcoast Uni Podiatric Unit</li>
    <li>BFRA Level 1 Barefoot Rehabilitation Instructor</li>
    <li>Foot Manual Therapies trained</li>
    <li>Fascial Lines trained</li>
    <li>Class 3b Laser Certified</li>
  </ul>
</div>
</body>
</html>
```